Dietitian needs awesome business card

I need a contemporary design that's eye catching but professional.
My card is to given to doctors, specialists and patients alike.
I manage patients with chronic diseases
I have uploaded my logo and current business card, I would also like the other Certified Clinical Nutritionist logo incorporated into the design

Target Market(s)

Doctors, specialists and patients

Industry/Entity Type

Healthcare

Contact Information for Business Card

www.brightfieldnutrition.com.au
Ph: 0427 561 903
Fax: 6457 2183
email: marcus.k.diet@fernmail.com
Space on the back of the card with: Appointment date, Appointment time and appointment location

Font styles to use
Serif

Colors
fbee3e
876aae
ffc214

Requirements
Must have
• My Logo
• Certified Clinical Nutritionist Logo
• My 4 locations - Pinebrook Medical Centre, North Corrin Health, Hollis Medical, Ashcombe Doctors Surgery
Nice to have
• I like the colours in my current business card

```html
<!DOCTYPE html>
<html lang="en">
<head>
<meta charset="utf-8">
<title>Brightfield Nutrition &amp; Dietetics – Business Card</title>
<link rel="stylesheet" href="https://fonts.googleapis.com/css2?family=Philosopher:wght@400&family=Asap:wght@400&family=Noto+Serif:wght@400&display=swap">
<style>
  :root {
    --bg: #8e8e8e;
    --card: #ffffff;
    --navy: #27388f;
    --icon-blue: #1d3f8f;
    --green: #7ab62a;
    --text-grey: #4a4a4a;
    --rule: #b4b4b4;
    --badge-orange: #f07b22;
    --band-green: #4b5a3a;
    --band-green-dark: #3c4a2e;
    --tab-light: #2f5fd0;
    --tab-dark: #1a2f86;
    --brief-yellow: #ffc214;
    --brief-lemon: #fbee3e;
    --brief-purple: #876aae;
  }
  * { margin: 0; padding: 0; box-sizing: border-box; }
  html, body { width: 1105px; height: 1200px; overflow: hidden; }
  body {
    background: var(--bg);
    position: relative;
    font-family: "Asap", Arial, sans-serif;
  }
  .card {
    position: absolute;
    left: 182px;
    width: 747px;
    height: 425px;
    background: var(--card);
    overflow: hidden;
  }
  .card--front { top: 120px; }
  .card--back { top: 636px; }

  /* Front */
  .brand {
    position: absolute;
    left: 50px;
    top: 52px;
    display: flex;
    align-items: center;
    gap: 14px;
    color: var(--navy);
    font-family: "Philosopher", "Trebuchet MS", sans-serif;
  }
  .brand__mark {
    width: 68px; height: 68px;
    border-radius: 50%;
    background: var(--navy);
    flex: none;
  }
  .brand__name { line-height: 1; }
  .brand__name-main { display: block; font-size: 46px; }
  .brand__name-sub { display: block; font-size: 19px; margin-top: 4px; }

  .contact {
    position: absolute;
    left: 52px;
    top: 260px;
    list-style: none;
    color: var(--text-grey);
    font-size: 19px;
  }
  .contact__item {
    display: flex;
    align-items: center;
    gap: 10px;
    height: 28.5px;
  }
  .contact__icon { width: 18px; height: 18px; fill: var(--icon-blue); flex: none; }

  .person {
    position: absolute;
    right: 47px;
    top: 284px;
    text-align: right;
    font-family: "Philosopher", "Trebuchet MS", sans-serif;
  }
  .person__name { font-size: 27px; color: var(--navy); line-height: 1.2; }
  .person__role { font-size: 20px; color: var(--green); line-height: 1.4; }

  .edge-tab {
    position: absolute;
    right: 0;
    top: 290px;
    width: 18px;
    height: 56px;
    background: linear-gradient(90deg, var(--tab-light), var(--tab-dark));
  }

  /* Back */
  .credential-badge {
    position: absolute;
    left: 119px;
    top: 61px;
    width: 178px;
    height: 84px;
    border-radius: 3px;
    background: var(--badge-orange);
  }
  .appointment {
    position: absolute;
    left: 345px;
    top: 48px;
    color: var(--navy);
    font-size: 20px;
  }
  .appointment__row { display: flex; align-items: baseline; height: 36px; }
  .appointment__fill {
    display: inline-block;
    border-bottom: 2px dotted var(--navy);
    margin-left: 6px;
    height: 1px;
  }
  .appointment__fill--date { width: 214px; }
  .appointment__fill--time { width: 150px; }
  .appointment__fill--location { width: 180px; }
  .appointment__suffix { font-size: 16px; margin-left: 6px; }

  .locations {
    position: absolute;
    left: 41px;
    top: 153px;
    width: 643px;
    list-style: none;
  }
  .locations__item {
    height: 43px;
    border-bottom: 1.5px solid var(--rule);
    display: flex;
    align-items: flex-end;
    gap: 10px;
    padding: 0 0 7px 4px;
    color: var(--text-grey);
    font-size: 17px;
  }
  .locations__box {
    width: 14px; height: 14px;
    border: 2px solid var(--brief-purple);
    border-radius: 2px;
    flex: none;
    margin-bottom: 3px;
  }

  .tagline-band {
    position: absolute;
    left: 0; bottom: 0;
    width: 100%;
    height: 63px;
    border-top: 4px solid var(--brief-yellow);
    background: linear-gradient(90deg, var(--band-green-dark), var(--band-green) 50%, var(--band-green-dark));
    display: flex;
    align-items: center;
    justify-content: center;
  }
  .tagline {
    font-family: "Noto Serif", Georgia, serif;
    color: #fff;
    font-size: 25px;
  }
</style>
</head>
<body>
  <section class="card card--front" aria-label="Card front">
    <div class="brand">
      <span class="brand__mark"></span>
      <span class="brand__name">
        <span class="brand__name-main">Brightfield</span>
        <span class="brand__name-sub">Nutrition &amp; Dietetics</span>
      </span>
    </div>

    <ul class="contact">
      <li class="contact__item">
        <svg class="contact__icon" viewBox="0 0 24 24" aria-hidden="true"><path d="M6.6 10.8a15.1 15.1 0 0 0 6.6 6.6l2.2-2.2a1 1 0 0 1 1-.25 11.4 11.4 0 0 0 3.6.57 1 1 0 0 1 1 1V20a1 1 0 0 1-1 1A17 17 0 0 1 3 4a1 1 0 0 1 1-1h3.5a1 1 0 0 1 1 1c0 1.25.2 2.45.57 3.57a1 1 0 0 1-.25 1z"/></svg>
        0427 561 903
      </li>
      <li class="contact__item">
        <svg class="contact__icon" viewBox="0 0 24 24" aria-hidden="true"><path d="M6 2h12v6H6z M3 9h18a1 1 0 0 1 1 1v7h-4v5H6v-5H2v-7a1 1 0 0 1 1-1z M8 15v5h8v-5z"/></svg>
        6457 2183
      </li>
      <li class="contact__item">
        <svg class="contact__icon" viewBox="0 0 24 24" aria-hidden="true"><path d="M2 5h20v14H2z M3.5 6.5 12 13l8.5-6.5" stroke="#fff" stroke-width="1.5"/></svg>
        marcus.k.diet@fernmail.com
      </li>
      <li class="contact__item">
        <svg class="contact__icon" viewBox="0 0 24 24" aria-hidden="true"><circle cx="12" cy="12" r="10"/><path d="M2 12h20M12 2c3 3 3 17 0 20M12 2c-3 3-3 17 0 20" stroke="#fff" stroke-width="1.3" fill="none"/></svg>
        brightfieldnutrition.com.au
      </li>
    </ul>

    <div class="person">
      <p class="person__name">Marcus Kellaway</p>
      <p class="person__role">Nutritionist &amp; Chef</p>
    </div>
    <div class="edge-tab"></div>
  </section>

  <section class="card card--back" aria-label="Card back">
    <div class="credential-badge" role="img" aria-label="Certified Clinical Nutritionist badge"></div>

    <div class="appointment">
      <div class="appointment__row">Date :<span class="appointment__fill appointment__fill--date"></span></div>
      <div class="appointment__row">Time :<span class="appointment__fill appointment__fill--time"></span><span class="appointment__suffix">AM/PM</span></div>
      <div class="appointment__row">Location :<span class="appointment__fill appointment__fill--location"></span></div>
    </div>

    <ul class="locations">
      <li class="locations__item"><span class="locations__box"></span>Pinebrook Medical Centre</li>
      <li class="locations__item"><span class="locations__box"></span>North Corrin Health</li>
      <li class="locations__item"><span class="locations__box"></span>Hollis Medical</li>
      <li class="locations__item"><span class="locations__box"></span>Ashcombe Doctors Surgery</li>
    </ul>

    <div class="tagline-band">
      <p class="tagline">Dietitian for Launceston &amp; North East Tasmania</p>
    </div>
  </section>
</body>
</html>
```